Redesign company trifold brochure

We are rebranding our company in September and looking for a more professional design for our brochure.

What we do - providing interdisciplinary care for those supporting ill, elderly and special needs pets at home following the human hospice model of care - is very novel and our brochure is key in explaining it and our offerings.

We serve dogs and cats. Most of the animals are quite sick, elderly. I have many personal and stock photos we can use in the brochure. Please - no pictures of puppies and/or kittens.

The hard part is fitting the info and message into a clear and concise format.

It must be appealing both to pet owners and vets (who are our primary source of patients through referrals).

It should covey WARMTH, COMPASSION, PROFESSIONALISM, and EXPERTISE.

Please look at our website www.TrellisAnimalRespite.com for more info

We have until now used maroon and copper for colors - to reflect the "sunset" of the pets life. BUT are now changing to Navy, Teal and White to reflect calm, trust and competence.

We will use the same logo recolored.

Existing brochure and new logo are attached.

PLEASE ask questions!!
Updates

We have a library of stock images you are welcome to use. All have been legally acquired and we have the right to use them. You DO NOT have to use them, just sending along in case you wish to. https://www.filecrate.example/sh/qk4vrm82zd1pyno/KLQ7Ztbn-Rrfx2mh9sWpYJ4Dc?dl=0

Our colors are NAVY, TEAL and WHITE. For your reference, the navy we use is 99/87/44/55 (CMYK) The Teal we use is 76/11/44/0 (CMYK) Thank you!

Designers -- pleaseuse pictures of older pets (no puppies or kittens). Below is a link to stock photos we own that would be appropriate for use in the brochure. https://www.filecrate.example/sh/w274m6t9pxkr5da/KLRn3GsfwlTVBXEPcq_8ZNj5u?dl=0 THANK YOU!

Designers -- I would VERY much like to include a photo of a pet in a wheel chair. I have personal photos as well as (purchased) stock photos for this purpose which can be found at http://lnk.example/TARHC-Pets-in-Wheelchairs Thank you!!

Today is the last day! Many of you have submitted beautiful designs and others are rolling in. I am so appreciative of your time and energy!! Please do not let the deadline pass without YOUR very BEST entry being submitted!! Thank you! - Miriam & All of us at Trellis Animal Respite & Home Care

Target Market(s)

Pet Owners and Veterinarians

Industry/Entity Type

Pet Care

Font styles to use
Serif

Colors
0455a3
33b8a4
ffffff

Requirements
Must have
• Our logo and information about our services. Pictures of pets. Our contact info. PLEASE NOTE: this is a 2 sided brochure. Please submit both inside and outside.
Should not have
• puppies, kittens - anything off message

```html
<!DOCTYPE html>
<html lang="en">
<head>
<meta charset="utf-8">
<title>Trellis Animal Respite &amp; Home Care – Trifold Brochure</title>
<link href="https://fonts.googleapis.com/css2?family=Quicksand:wght@400;500;600;700&family=Cormorant+Garamond:ital,wght@1,500;1,600&family=Italianno&display=swap" rel="stylesheet">
<style>
  :root {
    --backdrop: #e4e6e5;
    --teal: #33b8a4;
    --teal-bright: #6fe3cf;
    --navy: #0455a3;
    --navy-deep: #06305c;
    --white: #ffffff;
    --panel-light: #f3f7f7;
    --ink: #123a5e;
    --grass-top: #2f5e2a;
    --grass-mid: #3f8a34;
    --grass-deep: #0f3d1f;
    --coat-gold: #c98a3a;
    --coat-deep: #7d461a;
  }
  * { box-sizing: border-box; margin: 0; padding: 0; }
  html, body { width: 1200px; height: 900px; overflow: hidden; }
  body {
    background: var(--backdrop);
    font-family: "Quicksand", Arial, sans-serif;
    position: relative;
  }
  .brochure {
    position: absolute;
    left: 105px; top: 70px;
    width: 990px; height: 760px;
    display: flex;
    box-shadow: 0 10px 30px rgba(0,0,0,0.18);
  }
  .panel { position: relative; width: 330px; height: 760px; overflow: hidden; }

  /* Left panel: team and beliefs */
  .panel--beliefs { color: var(--white); }
  .panel--beliefs .photo-fill {
    position: absolute; inset: 0;
    background: linear-gradient(180deg, var(--grass-top) 0%, #356c2e 30%, var(--grass-mid) 50%, #24602a 72%, var(--grass-deep) 100%);
  }
  .panel--beliefs .shade {
    position: absolute; inset: 0;
    background: linear-gradient(180deg, rgba(6,48,92,0.55) 0%, rgba(6,48,92,0.25) 40%, rgba(6,48,92,0) 60%, rgba(6,48,92,0.35) 100%);
  }
  .panel--beliefs .content { position: relative; padding: 40px 26px 0 30px; }
  .team-list { list-style: none; color: var(--teal-bright); font-size: 14px; font-weight: 700; line-height: 1.5; text-shadow: 0 1px 2px rgba(0,0,0,0.45); }
  .team-list li { padding-left: 14px; position: relative; }
  .team-list li::before { content: "•"; position: absolute; left: 0; }
  .beliefs-title {
    font-family: "Italianno", "Times New Roman", serif;
    font-weight: 400; font-size: 56px; line-height: 1;
    margin: 130px 0 16px 60px;
    text-shadow: 0 1px 3px rgba(0,0,0,0.35);
  }
  .belief-list { list-style: none; font-size: 13.5px; font-weight: 500; line-height: 1.4; text-shadow: 0 1px 2px rgba(0,0,0,0.35); }
  .belief-list li { display: flex; gap: 8px; margin-bottom: 12px; }
  .belief-list svg { flex: none; width: 16px; height: 10px; margin-top: 5px; }

  /* Middle panel: contact */
  .panel--contact { background: var(--panel-light); color: var(--ink); border-top: 8px solid var(--navy); border-bottom: 8px solid var(--navy); }
  .contact-photo {
    position: absolute; top: 122px; left: 105px;
    width: 120px; height: 120px; border-radius: 50%;
    background: radial-gradient(circle at 40% 40%, #6b4a30, #3a2416 75%);
    border: 4px solid var(--teal);
  }
  .contact-heading {
    position: absolute; top: 282px; left: 0; width: 100%; text-align: center;
    font-family: "Cormorant Garamond", Georgia, serif; font-style: italic; font-weight: 600;
    font-size: 32px; color: var(--teal);
  }
  .contact-org {
    position: absolute; top: 334px; left: 0; width: 100%; text-align: center;
    font-size: 14px; font-weight: 700; color: var(--navy); padding: 0 30px;
  }
  .contact-list { position: absolute; top: 392px; left: 40px; list-style: none; }
  .contact-list li { display: flex; align-items: center; gap: 12px; font-size: 13px; font-weight: 500; color: var(--ink); margin-bottom: 18px; white-space: nowrap; }
  .contact-list .icon {
    flex: none; width: 26px; height: 26px; border-radius: 50%;
    background: var(--teal); display: flex; align-items: center; justify-content: center;
  }
  .contact-list svg { width: 14px; height: 14px; }

  /* Right panel: cover */
  .panel--cover { color: var(--white); }
  .panel--cover .photo-fill {
    position: absolute; inset: 0;
    background: linear-gradient(160deg, #2f5a24 0%, #5f9a40 16%, var(--coat-gold) 40%, #b5722b 62%, var(--coat-deep) 85%, #4d6f2a 100%);
  }
  .panel--cover .shade {
    position: absolute; inset: 0;
    background: linear-gradient(180deg, rgba(6,48,92,0.45) 0%, rgba(6,48,92,0) 28%, rgba(6,48,92,0) 60%, rgba(6,48,92,0.5) 100%);
  }
  .cover-tagline {
    position: absolute; top: 34px; right: 26px; width: 260px; text-align: right;
    font-size: 18px; font-weight: 600; line-height: 1.35;
    text-shadow: 0 1px 3px rgba(0,0,0,0.4);
  }
  .logo-band {
    position: absolute; top: 420px; left: 0; width: 100%; height: 90px;
    background: rgba(4,85,163,0.72);
    display: flex; align-items: center; gap: 14px; padding: 0 24px;
  }
  .logo-mark { flex: none; width: 32px; height: 32px; border-radius: 50%; background: var(--teal); }
  .logo-name { font-size: 17px; font-weight: 600; color: var(--white); line-height: 1.3; }
  .cover-promise {
    position: absolute; top: 560px; right: 30px; text-align: right;
    font-family: "Cormorant Garamond", Georgia, serif; font-style: italic; font-weight: 600;
    font-size: 28px; line-height: 1.15;
    text-shadow: 0 1px 3px rgba(0,0,0,0.45);
  }
</style>
</head>
<body>
<main class="brochure">

  <section class="panel panel--beliefs">
    <div class="photo-fill" role="img" aria-label="Photograph of a sunlit lawn with tall grass blades in the foreground"></div>
    <div class="shade"></div>
    <div class="content">
      <ul class="team-list">
        <li>Certified Thanatologists</li>
        <li>Certified Veterinary Technicians</li>
        <li>Interfaith Spiritual Advisor</li>
        <li>Certified Small Animal Massage Therapist</li>
        <li>Animal Care Specialists</li>
        <li>Hospice Assistants</li>
        <li>Client Care Coordinator</li>
      </ul>
      <h2 class="beliefs-title">We Believe</h2>
      <ul class="belief-list">
        <li><svg viewBox="0 0 16 10"><path d="M1 5h12M9 1l4 4-4 4" stroke="#fff" stroke-width="1.4" fill="none"/></svg><span>That animals are conscious beings, capable of thought, feelings, emotion and choice</span></li>
        <li><svg viewBox="0 0 16 10"><path d="M1 5h12M9 1l4 4-4 4" stroke="#fff" stroke-width="1.4" fill="none"/></svg><span>That each animal is an individual with his or her unique needs and wishes</span></li>
        <li><svg viewBox="0 0 16 10"><path d="M1 5h12M9 1l4 4-4 4" stroke="#fff" stroke-width="1.4" fill="none"/></svg><span>That all pets deserve to be pain-free</span></li>
        <li><svg viewBox="0 0 16 10"><path d="M1 5h12M9 1l4 4-4 4" stroke="#fff" stroke-width="1.4" fill="none"/></svg><span>That an interdisciplinary team is essential to addressing the needs of pets and their families through aging and illness</span></li>
        <li><svg viewBox="0 0 16 10"><path d="M1 5h12M9 1l4 4-4 4" stroke="#fff" stroke-width="1.4" fill="none"/></svg><span>That quality of life is subjective, best evaluated by the family who knows and loves the animal</span></li>
      </ul>
    </div>
  </section>

  <section class="panel panel--contact">
    <div class="contact-photo" role="img" aria-label="Round photograph of an older pet resting"></div>
    <h2 class="contact-heading">Contact Us</h2>
    <p class="contact-org">Trellis Animal Respite &amp; Home Care</p>
    <ul class="contact-list">
      <li><span class="icon"><svg viewBox="0 0 14 14"><path d="M3 1l2 3-1.2 1.2a7 7 0 0 0 5 5L10 9l3 2-1 2C6 13 1 8 1 2z" fill="#fff"/></svg></span>555.014.2287</li>
      <li><span class="icon"><svg viewBox="0 0 14 14"><path d="M3 1l2 3-1.2 1.2a7 7 0 0 0 5 5L10 9l3 2-1 2C6 13 1 8 1 2z" fill="#fff"/></svg></span>Fax 555.014.2290</li>
      <li><span class="icon"><svg viewBox="0 0 14 14"><rect x="1" y="3" width="12" height="8" fill="none" stroke="#fff" stroke-width="1.3"/><path d="M1 3l6 5 6-5" fill="none" stroke="#fff" stroke-width="1.3"/></svg></span>care@trellisanimalrespite.example</li>
      <li><span class="icon"><svg viewBox="0 0 14 14"><circle cx="7" cy="7" r="5.5" fill="none" stroke="#fff" stroke-width="1.2"/><path d="M1.5 7h11M7 1.5c-3 3-3 8 0 11M7 1.5c3 3 3 8 0 11" fill="none" stroke="#fff" stroke-width="1"/></svg></span>www.TrellisAnimalRespite.com</li>
      <li><span class="icon"><svg viewBox="0 0 14 14"><path d="M7 13s-4.5-4.5-4.5-7.5a4.5 4.5 0 0 1 9 0C11.5 8.5 7 13 7 13z" fill="#fff"/><circle cx="7" cy="5.5" r="1.6" fill="#33b8a4"/></svg></span>PO Box 214, Harwick, MA 01890</li>
    </ul>
  </section>

  <section class="panel panel--cover">
    <div class="photo-fill" role="img" aria-label="Photograph of a senior golden retriever lying in green grass"></div>
    <div class="shade"></div>
    <p class="cover-tagline">Skilled Home Care for Ill, Elderly and Special Needs Animals</p>
    <div class="logo-band">
      <span class="logo-mark"></span>
      <span class="logo-name">Trellis Animal Respite<br>&amp; Home Care</span>
    </div>
    <p class="cover-promise">Compassionate<br>Support for Families</p>
  </section>

</main>
</body>
</html>
```